Web Design for Independent Pet Supply shop.

Larch Critter Depot is a locally owned and operated premium natural pet food store and supply company with 2 thriving retail stores in Bend, Oregon, and a home delivery service. The pet food offered is the best on the market and may be described as “holistic”. Also on offer is a vast selection of toys, training tools, treats, and other supplies, as well as dog washing services that range from "do-it yourself" to "spa." Current site: LarchCritterDepot.com. They need a new, updated and responsive site.
Likes:
Tovanels.com: Natural colors, not loud, pages in motion, simple & clean but very informative.
Dorvikmerin.com: Everything in simple big colorful blocks. The specials run across the top and in motion. This site looks very professional but simple. The information is available several different places.
Plenharvest.com: Again big blocks through out. Very Fun and inviting. Tons of information with videos and recipes and testimonials. Pleasant feel and colors as well.
Dislikes:
Furlix.com: Looks cheap, hate the colors, very busy and over whelming. Hate the old style header bar going across with options. Too many printed words instead of fun images.
Colors should be "natural" tones, warm and soothing. Deep dark blue and greys with earthy wood color.
Do Not Use: Blue violet, violet, red violet

```html
<!DOCTYPE html>
<html lang="en">
<head>
<meta charset="utf-8">
<title>Larch Critter Depot</title>
<link rel="stylesheet" href="https://fonts.googleapis.com/css2?family=Marcellus&family=PT+Sans:ital,wght@0,400;0,700;1,400&family=PT+Sans+Narrow:wght@400;700&display=swap">
<style>
:root{
  --navy:#0f1a45;
  --navy-deep:#0a1436;
  --wood:#a9803f;
  --wood-light:#b8904e;
  --grey-band:#f4f4f4;
  --ink:#2d2d2d;
  --white:#ffffff;
}
*{margin:0;padding:0;box-sizing:border-box}
html,body{width:696px;height:1200px;overflow:hidden;background:var(--white)}
body{position:relative;font-family:"PT Sans",sans-serif;color:var(--ink)}
.abs{position:absolute}

/* header */
.site-header{left:0;top:0;width:696px;height:54px;background:var(--navy)}
.brand{display:flex;align-items:center;gap:4px;font-family:"PT Sans Narrow",sans-serif;font-weight:700;color:var(--wood);text-transform:uppercase;white-space:nowrap}
.brand-dot{border-radius:50%;background:var(--wood);flex:none}
.site-header .brand{left:114px;top:20px;font-size:10.5px;line-height:12px}
.site-header .brand-dot{width:9px;height:9px}
.main-nav{left:238px;top:19px;display:flex;font-size:8px;color:var(--white)}
.main-nav a{color:inherit;text-decoration:none;padding:3px 0;margin-right:12px;line-height:10px}
.main-nav a.active{background:var(--wood);padding:3px 13px;margin-right:14px}

/* hero */
.hero{left:0;top:54px;width:696px;height:312px;background:linear-gradient(120deg,#c9cdd3 0%,#a58e74 35%,#b7722f 55%,#8f6a4a 75%,#c2c6cc 100%);overflow:hidden}
.hero-cut{left:0;top:0}
.hero-title{left:0;top:84px;width:696px;text-align:center;font-family:"Marcellus",serif;font-size:23px;line-height:28px;color:var(--white);letter-spacing:.3px;font-weight:400}
.hero-text{left:180px;top:120px;width:336px;text-align:center;font-size:6.3px;line-height:7.6px;color:var(--white)}
.hero-btn{left:307px;top:152px;width:71px;height:22px;background:var(--navy);color:var(--white);font-size:8px;text-align:center;line-height:22px}
.hero-arrow{top:96px;font-size:24px;line-height:28px;color:var(--navy);font-family:"PT Sans",sans-serif;font-weight:700}
.hero-dots{left:316px;top:201px;display:flex;gap:8px}
.hero-dots span{width:8px;height:8px;border-radius:50%;background:#3a3a3a}
.hero-dots span.on{background:var(--wood)}

/* features */
.feature{width:170px;text-align:center}
.feature-icon{display:block;margin:0 auto}
.feature p{font-size:9.5px;line-height:11px;color:#333;margin-top:8px}
.feature a{display:block;margin-top:9px;font-size:6.5px;font-style:italic;color:var(--wood)}

/* products */
.products{left:0;top:500px;width:696px;height:338px;background:var(--grey-band)}
.section-title{font-family:"PT Sans Narrow",sans-serif;font-weight:700;font-size:14px;text-transform:uppercase}
.products .section-title{left:106px;top:41px;color:var(--navy)}
.product-img{width:94px;height:93px;background:linear-gradient(90deg,var(--navy) 0 60%,#c0241f 60% 100%)}
.product-name{font-family:"PT Sans Narrow",sans-serif;font-weight:700;font-size:9.5px;color:var(--navy);text-transform:uppercase}
.product-text{width:122px;font-size:6.4px;line-height:8.2px;color:#333}
.btn-small{width:40px;height:13px;font-size:6px;line-height:13px;text-align:center;color:var(--white);border-radius:1px}
.btn-navy{background:var(--navy)}
.btn-wood{background:var(--wood-light)}

/* news */
.news{left:0;top:838px;width:696px;height:184px;background:linear-gradient(100deg,#142556 0%,#1c2d5e 50%,#15244f 100%)}
.news .section-title{left:115px;top:40px;color:var(--white);font-size:15px}
.news-photo{width:63px;height:64px;background:linear-gradient(160deg,#3d3630,#8a6a54 50%,#2c3f6d)}
.news-title{font-family:"PT Sans Narrow",sans-serif;font-weight:700;font-size:12px;color:var(--white)}
.news-date{font-size:6px;font-style:italic;font-weight:700;color:var(--white)}
.news-text{width:150px;font-size:6.4px;line-height:8px;color:var(--white)}
.btn-news{width:46px;height:14px;font-size:7px;line-height:14px;text-align:center;border-radius:1px}
.btn-light{background:#f2f2f2;color:#333}
.news-arrows{left:572px;top:150px;font-size:13px;font-weight:700;color:var(--white);letter-spacing:2px}

/* footer */
.site-footer .brand{left:122px;top:1063px;font-size:13px;line-height:15px}
.site-footer .brand-dot{width:11px;height:11px}
.footer-about{left:125px;top:1092px;width:118px;font-size:7.5px;line-height:9px;color:#333}
.footer-about p+p{margin-top:9px}
.footer-col h4{font-family:"PT Sans Narrow",sans-serif;font-weight:700;font-size:9.5px;color:#333;text-transform:uppercase;margin-bottom:6px}
.footer-col li{list-style:none;font-size:7px;line-height:11px;color:#333}
.contact-row{display:flex;font-size:7px;line-height:12px;color:#333}
.contact-row span:first-child{width:41px}
</style>
</head>
<body>

<header class="site-header abs">
  <div class="brand abs"><span class="brand-dot"></span>Larch Critter Depot</div>
  <nav class="main-nav abs">
    <a class="active" href="#">Home</a><a href="#">Events</a><a href="#">Blog</a><a href="#">About</a><a href="#">Dog Wash</a><a href="#">Resources</a><a href="#">Products</a><a href="#">Links</a><a href="#">Contact</a>
  </nav>
</header>

<section class="hero abs" role="img" aria-label="Golden retriever resting with its tongue out">
  <h1 class="hero-title abs">WELCOME TO LARCH CRITTER DEPOT</h1>
  <p class="hero-text abs">Lorem ipsum dolor sit amet, consectetur adipisicing elit, sed do eiusmod tempor incididunt ut labore et dolore magna aliqua. Ut enim ad minim veniam, quis nostrud exercitation ullamco laboris nisi ut aliquip ex ea commodo consequat. Duis aute irure dolor in reprehenderit in voluptate velit esse cillum dolore eu fugiat nulla pariatur.</p>
  <div class="hero-btn abs">READ MORE</div>
  <span class="hero-arrow abs" style="left:112px">&#10094;</span>
  <span class="hero-arrow abs" style="left:556px">&#10095;</span>
  <div class="hero-dots abs"><span class="on"></span><span></span><span></span></div>
  <svg class="hero-cut abs" width="696" height="312" viewBox="0 0 696 312"><polygon points="0,308 696,172 696,312 0,312" fill="#ffffff"/></svg>
</section>

<div class="feature abs" style="left:93px;top:355px">
  <svg class="feature-icon" width="46" height="46" viewBox="0 0 46 46"><circle cx="23" cy="23" r="23" fill="#0f1a45"/><path d="M11 24 L23 12 L35 24 L32 24 L32 34 L26 34 L26 27 L20 27 L20 34 L14 34 L14 24 Z" fill="#fff"/></svg>
  <p>Lorem ipsum dolor sit amet,<br>consectetur dipisicing elit, sed do</p>
  <a>Continue reading...</a>
</div>
<div class="feature abs" style="left:265px;top:355px">
  <svg class="feature-icon" width="46" height="46" viewBox="0 0 46 46"><circle cx="23" cy="23" r="23" fill="#0f1a45"/><path d="M18 26 L14 36 L19 34 L21 38 L24 29 Z M28 26 L32 36 L27 34 L25 38 L22 29 Z" fill="#fff"/><circle cx="23" cy="20" r="9" fill="#fff"/><circle cx="23" cy="20" r="6" fill="none" stroke="#0f1a45" stroke-width="1.2"/><rect x="22.3" y="16.5" width="1.4" height="6" fill="#0f1a45"/></svg>
  <p>Lorem ipsum dolor sit amet,<br>consectetur dipisicing elit, sed do</p>
  <a>Continue reading...</a>
</div>
<div class="feature abs" style="left:432px;top:355px">
  <svg class="feature-icon" width="46" height="46" viewBox="0 0 46 46"><circle cx="23" cy="23" r="23" fill="#0f1a45"/><rect x="19" y="12" width="8" height="5" rx="1" fill="none" stroke="#fff" stroke-width="2"/><rect x="11" y="16" width="24" height="18" rx="3" fill="#fff"/><rect x="21.5" y="19" width="3" height="12" fill="#0f1a45"/><rect x="17" y="23.5" width="12" height="3" fill="#0f1a45"/></svg>
  <p>Lorem ipsum dolor sit amet,<br>consectetur dipisicing elit, sed do</p>
  <a>Continue reading...</a>
</div>

<section class="products abs">
  <h2 class="section-title abs">Our Products</h2>

  <div class="product-img abs" style="left:107px;top:68px" role="img" aria-label="Bag of dry dog food beside a bowl of kibble"></div>
  <h3 class="product-name abs" style="left:217px;top:79px">Product Name</h3>
  <p class="product-text abs" style="left:217px;top:94px">Lorem ipsum dolor sit amet, consectetur adipisicing elit, sed do eiusmod tempor incididunt ut labore et dolore magna aliqua. Ut enim ad minim veniam, quis nostrud exercitation ullamco laboris nisi</p>
  <div class="btn-small btn-navy abs" style="left:217px;top:141px">Read More</div>

  <div class="product-img abs" style="left:361px;top:68px" role="img" aria-label="Bag of dry dog food beside a bowl of kibble"></div>
  <h3 class="product-name abs" style="left:470px;top:79px">Product Name</h3>
  <p class="product-text abs" style="left:470px;top:94px">Lorem ipsum dolor sit amet, consectetur adipisicing elit, sed do eiusmod tempor incididunt ut labore et dolore magna aliqua. Ut enim ad minim veniam, quis nostrud exercitation ullamco laboris nisi</p>
  <div class="btn-small btn-wood abs" style="left:470px;top:141px">Read More</div>

  <div class="product-img abs" style="left:107px;top:190px" role="img" aria-label="Bag of dry dog food beside a bowl of kibble"></div>
  <h3 class="product-name abs" style="left:217px;top:201px">Product Name</h3>
  <p class="product-text abs" style="left:217px;top:216px">Lorem ipsum dolor sit amet, consectetur adipisicing elit, sed do eiusmod tempor incididunt ut labore et dolore magna aliqua. Ut enim ad minim veniam, quis nostrud exercitation ullamco laboris nisi</p>
  <div class="btn-small btn-wood abs" style="left:217px;top:263px">Read More</div>

  <div class="product-img abs" style="left:361px;top:190px" role="img" aria-label="Bag of dry dog food beside a bowl of kibble"></div>
  <h3 class="product-name abs" style="left:470px;top:201px">Product Name</h3>
  <p class="product-text abs" style="left:470px;top:216px">Lorem ipsum dolor sit amet, consectetur adipisicing elit, sed do eiusmod tempor incididunt ut labore et dolore magna aliqua. Ut enim ad minim veniam, quis nostrud exercitation ullamco laboris nisi</p>
  <div class="btn-small btn-wood abs" style="left:470px;top:263px">Read More</div>
</section>

<section class="news abs">
  <h2 class="section-title abs">News &amp; Events</h2>

  <div class="news-photo abs" style="left:117px;top:72px" role="img" aria-label="Portrait photo for the news story"></div>
  <h3 class="news-title abs" style="left:193px;top:72px">Take a closer look.</h3>
  <p class="news-date abs" style="left:193px;top:88px">Aug 17, 2012 &bull; 4</p>
  <p class="news-text abs" style="left:193px;top:102px">Proin gravida nibh vel velit auctor aliquet. Aenean sollicitudin, lorem quis bibendum auctor, nisi elit</p>
  <div class="btn-news btn-light abs" style="left:194px;top:122px">Read More</div>

  <div class="news-photo abs" style="left:378px;top:72px" role="img" aria-label="Portrait photo for the news story"></div>
  <h3 class="news-title abs" style="left:454px;top:72px">Take a closer look.</h3>
  <p class="news-date abs" style="left:454px;top:88px">Aug 17, 2012 &bull; 4</p>
  <p class="news-text abs" style="left:454px;top:102px">Proin gravida nibh vel velit auctor aliquet. Aenean sollicitudin, lorem quis bibendum auctor, nisi elit</p>
  <div class="btn-news btn-wood abs" style="left:455px;top:122px;color:#fff">Read More</div>

  <div class="news-arrows abs">&#10094;&#10095;</div>
</section>

<footer class="site-footer">
  <div class="brand abs"><span class="brand-dot"></span>Larch Critter Depot</div>
  <div class="footer-about abs">
    <p>Your about us information would fit here nicely.</p>
    <p>You could also just have an overview and use the link below to link to you full about us page.</p>
  </div>
  <div class="footer-col abs" style="left:282px;top:1066px">
    <h4>Company</h4>
    <ul><li>Home</li><li>Events</li><li>Blog</li><li>About</li><li>Dog Wash</li><li>Resources</li><li>Products</li><li>Link</li><li>Contact</li></ul>
  </div>
  <div class="footer-col abs" style="left:374px;top:1066px">
    <h4>Follow Us</h4>
    <ul style="line-height:12.5px"><li>Circlecast</li><li>Chirply</li><li>Friendwall</li><li>Workline</li><li>RSS</li></ul>
  </div>
  <div class="footer-col abs" style="left:462px;top:1065px">
    <h4>Contact Us</h4>
    <div class="contact-row"><span>Telephone</span><span>+1400 555 014</span></div>
    <div class="contact-row"><span>FAX</span><span>+1504 555 0178</span></div>
    <div class="contact-row"><span>E-mail</span><span>larchcritterdepot.com</span></div>
  </div>
</footer>

</body>
</html>
```